Luxury Business Card Design for High-End Window Treatments

Gilded Slatworks
Custom Plantation Shutters & Architectural Shading Systems

⸻

BACK

Daniel Trevick
Owner

Custom Interior & Exterior Window Treatments

919-555-0148
gildedslatworks.com

I have included a picture that I’m hoping we can use on the back, but I’m also wondering if you can get rid of the ladder? Should we get rid of shutters , shades and blinds underneath Gilded Slatworks?

Target Market(s)

High-end residential homeowners, custom home builders, architects, interior designers, and luxury renovation clients seeking premium plantation shutters and motorized architectural shading systems.

Industry/Entity Type

Custom Window treatments

Contact Information for Business Card

Front Gilded Slatworks Custom Plantation Shutters Motorized Architectural Shading Systems BACK Daniel Trevick Owner 919-555-0148 GildedSlatworks.com Custom Interior & Exterior Window Treatments By Appointment

Requirements
Nice to have
• Not 100% sure on nice to halves or the color but you can definitely check out my website to get a better understanding of what I’m trying to do

```html
<!DOCTYPE html>
<html lang="en">
<head>
<meta charset="utf-8">
<title>Gilded Slatworks Business Cards</title>
<link rel="stylesheet" href="https://fonts.googleapis.com/css2?family=Lora:wght@400;500&family=Open+Sans:wght@400&display=swap">
<style>
  :root {
    --backdrop: #3a3a3a;
    --card: #262626;
    --card-edge: #1c1c1c;
    --gold: #c9a23c;
    --gold-soft: #d4ae4a;
    --ink-light: #ffffff;
    --sky: #8fb3de;
    --foliage: #5b6a3e;
  }
  * { box-sizing: border-box; margin: 0; padding: 0; }
  html, body {
    width: 1200px; height: 758px; overflow: hidden;
    background: var(--backdrop);
  }
  .stage { position: relative; width: 1200px; height: 758px; }
  .card {
    position: absolute; top: 225px;
    width: 540px; height: 309px;
    border-radius: 18px;
    background: var(--card);
    overflow: hidden;
    box-shadow: 0 18px 40px rgba(0,0,0,.45);
  }
  .card--front { left: 40px; }
  .card--back { left: 620px; }

  /* Front */
  .front-brand {
    position: absolute; left: 0; right: 0; top: 96px;
    text-align: center;
    font-family: "Lora", serif; font-weight: 400;
    font-size: 46px; line-height: 1.05;
    color: var(--gold);
  }
  .front-services {
    position: absolute; left: 0; right: 0; top: 214px;
    display: flex; justify-content: center; gap: 28px;
    font-family: "Lora", serif; font-weight: 500;
    font-size: 22px; letter-spacing: 1px;
    color: var(--gold);
  }

  /* Back */
  .back-art { position: absolute; inset: 0; }
  .back-brand {
    position: absolute; left: 34px; top: 46px;
    font-family: "Lora", serif; font-weight: 400;
    font-size: 27px; line-height: 1.05;
    color: var(--gold);
  }
  .name-band {
    position: absolute; left: 34px; top: 140px;
  }
  .name-band__name {
    font-family: "Lora", serif; font-weight: 500;
    font-size: 24px; letter-spacing: .5px;
    text-transform: uppercase;
    color: var(--ink-light);
  }
  .name-band__role {
    font-family: "Open Sans", sans-serif; font-size: 14px;
    color: var(--ink-light); margin-top: 1px;
  }
  .back-tagline {
    position: absolute; left: 34px; top: 208px;
    font-family: "Lora", serif; font-weight: 500;
    font-size: 15px; line-height: 1.3;
    color: var(--gold);
  }
  .contact-list {
    position: absolute; left: 34px; top: 252px;
    list-style: none;
    font-family: "Lora", serif; font-size: 14px;
    color: var(--ink-light);
  }
  .contact-list li { display: flex; align-items: center; gap: 8px; height: 22px; }
  .contact-list svg { width: 15px; height: 15px; flex: none; }
</style>
</head>
<body>
<main class="stage">

  <section class="card card--front" aria-label="Card front">
    <h1 class="front-brand">Gilded<br>Slatworks</h1>
    <p class="front-services"><span>Shutters</span><span>Shades</span><span>Blinds</span></p>
  </section>

  <section class="card card--back" aria-label="Card back">
    <svg class="back-art" viewBox="0 0 540 309" width="540" height="309" aria-hidden="false">
      <defs>
        <linearGradient id="photoTones" x1="0" y1="0" x2="0" y2="1">
          <stop offset="0" stop-color="#8fb3de"/>
          <stop offset=".45" stop-color="#4c5566"/>
          <stop offset=".75" stop-color="#5b6a3e"/>
          <stop offset="1" stop-color="#9a8f7a"/>
        </linearGradient>
      </defs>
      <rect class="name-band-shape" x="0" y="130" width="340" height="56" fill="var(--gold)"/>
      <circle cx="478" cy="92" r="222" fill="var(--gold)"/>
      <circle cx="478" cy="92" r="212" fill="var(--card)"/>
      <circle cx="484" cy="88" r="200" fill="url(#photoTones)" role="img" aria-label="Photo of a two-storey house with a covered porch, white columns, shrubs and lawn chairs"/>
    </svg>

    <h2 class="back-brand">Gilded<br>Slatworks</h2>

    <div class="name-band">
      <p class="name-band__name">Daniel Trevick</p>
      <p class="name-band__role">Owner</p>
    </div>

    <p class="back-tagline">Custom Interior &amp; Exterior<br>Window Treatments</p>

    <ul class="contact-list">
      <li>
        <svg viewBox="0 0 16 16" aria-hidden="true"><circle cx="8" cy="8" r="8" fill="#c9a23c"/><path d="M5 4.5c.6-.4 1.1-.2 1.4.4l.5 1c.2.4 0 .8-.3 1l-.4.3c.4.9 1 1.5 1.9 1.9l.3-.4c.2-.3.6-.5 1-.3l1 .5c.6.3.8.8.4 1.4-.5.8-1.4 1-2.3.6-1.9-.8-3.3-2.2-4.1-4.1-.4-.9-.2-1.8.6-2.3z" fill="#262626"/></svg>
        919-555-0148
      </li>
      <li>
        <svg viewBox="0 0 16 16" aria-hidden="true"><circle cx="8" cy="8" r="8" fill="#c9a23c"/><circle cx="8" cy="8" r="4.3" fill="none" stroke="#262626" stroke-width="1.1"/><path d="M3.7 8h8.6M8 3.7c-1.6 2.4-1.6 6.2 0 8.6M8 3.7c1.6 2.4 1.6 6.2 0 8.6" fill="none" stroke="#262626" stroke-width="1"/></svg>
        gildedslatworks.com
      </li>
    </ul>
  </section>

</main>
</body>
</html>
```